Thornvale Group needs a business card design

We need a new business card design using the logo recently selected in a logo competition on Pixel Bazaar. Our business is a consultancy specializing in aviation and energy and the winning business card design will promote an image of precision and professionalism with creativity.

Please use the logo with the name on the front of the card and use a complementary font. Make the back white with either the light grey or dark grey logo.

Target Market(s)

Senior finance and legal leaders at aviation and energy companies

Industry/Entity Type

Management Consulting

Contact Information for Business Card

Peter Castrell
President
Thornvale Group

www.thornvalegroup.example

(555) 204-6391
pc@thornvalegroup.example

Requirements
Must have
• Professional font that goes well with the logo font

```html
<!DOCTYPE html>
<html lang="en">
<head>
<meta charset="utf-8">
<title>Thornvale Group – Business Card</title>
<link rel="stylesheet" href="https://fonts.googleapis.com/css2?family=Open+Sans:wght@400;600;700&display=swap">
<style>
  :root {
    --navy: #0f3e6e;
    --ink-grey: #555a60;
    --card-white: #ffffff;
    --backdrop: #e9ebee;
    --card-edge: rgba(0, 0, 0, 0.10);
  }
  * { margin: 0; padding: 0; box-sizing: border-box; }
  html, body {
    width: 1200px;
    height: 900px;
    overflow: hidden;
    background: var(--backdrop);
    font-family: "Open Sans", sans-serif;
  }
  .canvas {
    position: relative;
    width: 1200px;
    height: 900px;
  }
  .card {
    position: absolute;
    background: var(--card-white);
    box-shadow: 0 2px 10px var(--card-edge);
    overflow: hidden;
  }

  /* Front */
  .card-front { left: 238px; top: 62px; width: 555px; height: 342px; }
  .corner { position: absolute; }
  .corner-top-right { right: 0; top: 0; width: 113px; height: 88px; }
  .corner-bottom-left { left: 0; bottom: 0; width: 107px; height: 92px; }

  .brand-front {
    position: absolute;
    left: 50px;
    top: 112px;
    width: 205px;
    text-align: center;
    color: var(--navy);
  }
  .brand-mark {
    display: block;
    width: 26px;
    height: 26px;
    margin: 0 auto 16px;
    background: var(--navy);
  }
  .brand-name-front {
    font-size: 24px;
    font-weight: 400;
    line-height: 1.2;
    letter-spacing: 2px;
  }
  .brand-name-front .spaced { letter-spacing: 9px; font-size: 16px; }

  .contact {
    position: absolute;
    left: 298px;
    top: 120px;
  }
  .contact-name {
    font-size: 18px;
    font-weight: 700;
    color: var(--navy);
    line-height: 1.2;
  }
  .contact-title {
    font-size: 14px;
    color: var(--ink-grey);
    line-height: 1.3;
    margin-bottom: 26px;
  }
  .contact-line {
    display: flex;
    align-items: center;
    gap: 8px;
    font-size: 14px;
    color: var(--ink-grey);
    line-height: 20px;
  }
  .contact-line svg { width: 12px; height: 12px; flex: none; fill: var(--navy); }

  /* Back */
  .card-back { left: 457px; top: 518px; width: 560px; height: 343px; text-align: center; }
  .brand-back {
    position: absolute;
    left: 0; right: 0;
    top: 96px;
    color: var(--navy);
    font-weight: 400;
  }
  .brand-back .brand-line-main { font-size: 46px; letter-spacing: 3px; line-height: 1.1; }
  .brand-back .brand-line-sub { font-size: 24px; letter-spacing: 24px; line-height: 1.6; padding-left: 24px; }

  .tagline {
    position: absolute;
    left: 0; right: 0;
    top: 244px;
    font-size: 16px;
    font-weight: 700;
    color: var(--navy);
    letter-spacing: -0.3px;
  }
  .sectors {
    position: absolute;
    left: 0; right: 0;
    top: 270px;
    font-size: 16px;
    color: var(--ink-grey);
    letter-spacing: -0.3px;
  }
</style>
</head>
<body>
<main class="canvas">

  <section class="card card-front" aria-label="Card front">
    <svg class="corner corner-top-right" viewBox="0 0 113 88" aria-hidden="true">
      <polygon points="0,0 113,0 113,88" fill="var(--navy)"/>
    </svg>
    <svg class="corner corner-bottom-left" viewBox="0 0 107 92" aria-hidden="true">
      <polygon points="0,0 107,92 0,92" fill="var(--navy)"/>
    </svg>

    <div class="brand-front">
      <span class="brand-mark"></span>
      <div class="brand-name-front">THORNVALE<br><span class="spaced">GROUP</span></div>
    </div>

    <div class="contact">
      <p class="contact-name">Peter J. Castrell</p>
      <p class="contact-title">President</p>
      <p class="contact-line">
        <svg viewBox="0 0 24 24" aria-hidden="true"><path d="M6.6 10.8a15.1 15.1 0 0 0 6.6 6.6l2.2-2.2c.3-.3.7-.4 1-.2 1.1.4 2.3.6 3.6.6.6 0 1 .4 1 1V20c0 .6-.4 1-1 1C10.6 21 3 13.4 3 4c0-.6.4-1 1-1h3.5c.6 0 1 .4 1 1 0 1.3.2 2.5.6 3.6.1.3 0 .7-.2 1z"/></svg>
        (555) 204-6391
      </p>
      <p class="contact-line">
        <svg viewBox="0 0 24 24" aria-hidden="true"><path d="M2 5h20v14H2z M3.5 6.5 12 13l8.5-6.5" fill="var(--navy)"/><path d="M3.5 6.5 12 13l8.5-6.5" fill="none" stroke="#fff" stroke-width="1.6"/></svg>
        pc@thornvalegroup.example
      </p>
    </div>
  </section>

  <section class="card card-back" aria-label="Card back">
    <div class="brand-back">
      <div class="brand-line-main">THORNVALE</div>
      <div class="brand-line-sub">GROUP</div>
    </div>
    <p class="tagline">Finance and Strategy Consulting</p>
    <p class="sectors">Aviation - Manufacturing - Energy</p>
  </section>

</main>
</body>
</html>
```